Website for my photography business

I need a website for my photography business, Bram Kellet Photography. I need a website that has a landing page with a cover photo of each kind of photography I do. For example, Nature, Weddings, Portraits and Architecture. I want it so that when someone comes onto my website they have to choose which kind of photography page they want to visit. So if they click on the wedding photo it will open to a page with my wedding portfolio images and a contact me button. If they choose nature photography I want them to be redirected to an e-commerce section where they can purchase prints. Architecture and Portraits should open up to their respective portfolios with about me and contact info. I like this kind of format because I want people who come to my website for a specific type of photography to be able to be directed there easily without having to look at a mix of other kinds of photography. I will provide a few files to use as placeholders. I have already purchased the bramkelletphotography.example domain name. A Wix website would be great because I am most familiar with it but I am open to anything.

Industry/Entity Type

Photographer

Number of Pages Required

5+ page

Requirements
Must have
• Landing Page and e-commerce

```html
<!DOCTYPE html>
<html lang="en">
<head>
<meta charset="utf-8">
<title>Bram Kellet Photography – Weddings</title>
<link rel="stylesheet" href="https://fonts.googleapis.com/css2?family=Dancing+Script:wght@400;500&family=Lora:ital@1&family=Raleway:ital,wght@0,400;0,500;1,500&display=swap">
<style>
  :root {
    --ink: #2b2b2b;
    --frame: #2e2e2e;
    --muted: #b9b9b9;
    --rule: #c9c9c9;
    --soft: #555555;
    --paper: #ffffff;
  }
  * { box-sizing: border-box; margin: 0; padding: 0; }
  html, body { width: 1200px; height: 868px; overflow: hidden; background: var(--paper); }
  body { position: relative; color: var(--ink); }

  .site-header {
    position: absolute; left: 236px; top: 43px; width: 731px; height: 142px;
    border: 2px solid var(--frame); text-align: center;
  }
  .brand-title {
    font-family: "Dancing Script", cursive; font-weight: 400;
    font-size: 46px; line-height: 1; margin-top: 5px; color: var(--ink);
  }
  .brand-tagline {
    font-family: "Dancing Script", cursive; font-size: 19px; line-height: 1;
    margin-top: 1px; color: var(--ink);
  }
  .main-nav {
    display: flex; justify-content: center; margin-top: 16px;
    font-family: "Lora", serif; font-style: italic; font-size: 14.5px;
  }
  .main-nav a {
    color: var(--ink); text-decoration: none; padding: 6px 13px;
    border-left: 1px solid var(--rule);
  }
  .main-nav a:first-child { border-left: none; }
  .main-nav a.is-current { color: var(--muted); }

  .gallery-mosaic { position: absolute; left: 0; top: 0; }

  .story-line {
    position: absolute; left: 480px; top: 693px; width: 250px; text-align: center;
    font-family: "Raleway", sans-serif; font-style: italic; font-weight: 500;
    font-size: 18px; line-height: 18px; color: var(--ink);
  }
  .contact-button {
    position: absolute; left: 546px; top: 751px; width: 112px; height: 22px;
    display: flex; align-items: center; justify-content: center; gap: 6px;
    font-family: "Raleway", sans-serif; font-size: 11.5px; letter-spacing: 0.8px;
    color: var(--ink); text-decoration: none;
  }
  .copyright {
    position: absolute; left: 0; width: 1200px; top: 803px; text-align: center;
    font-family: "Lora", serif; font-style: italic; font-size: 11px; color: var(--soft);
  }
  .social-links {
    position: absolute; left: 0; width: 1200px; top: 848px;
    display: flex; justify-content: center; gap: 16px;
    font-family: "Raleway", sans-serif; font-size: 11px; font-weight: 500;
  }
  .social-links a {
    color: var(--ink); text-decoration: none;
    display: flex; align-items: center; gap: 5px;
  }
  .social-dot { width: 12px; height: 12px; border-radius: 50%; background: var(--ink); }
</style>
</head>
<body>
  <header class="site-header">
    <h1 class="brand-title">Bram Kellet Photography</h1>
    <p class="brand-tagline">Creating extraordinary images that last infinetly</p>
    <nav class="main-nav">
      <a href="#">Home</a>
      <a href="#">Architecture</a>
      <a href="#">Portraits</a>
      <a href="#" class="is-current">Weddings</a>
      <a href="#">Nature</a>
      <a href="#">Contact me</a>
    </nav>
  </header>

  <svg class="gallery-mosaic" width="1200" height="868" viewBox="0 0 1200 868">
    <defs>
      <linearGradient id="tone-gold" x1="0" y1="0" x2="1" y2="1"><stop offset="0" stop-color="#bcb49a"/><stop offset="0.45" stop-color="#e6dcae"/><stop offset="1" stop-color="#faf3c0"/></linearGradient>
      <linearGradient id="tone-sky" x1="0" y1="0" x2="1" y2="1"><stop offset="0" stop-color="#e2ebea"/><stop offset="0.6" stop-color="#c9d6d8"/><stop offset="1" stop-color="#56606a"/></linearGradient>
      <linearGradient id="tone-rose" x1="0" y1="0" x2="1" y2="1"><stop offset="0" stop-color="#8d8088"/><stop offset="0.5" stop-color="#e6dccb"/><stop offset="1" stop-color="#bfc49a"/></linearGradient>
      <linearGradient id="tone-forest" x1="0" y1="0" x2="1" y2="1"><stop offset="0" stop-color="#4f6238"/><stop offset="0.55" stop-color="#9aa186"/><stop offset="1" stop-color="#e4e1d8"/></linearGradient>
      <linearGradient id="tone-gazebo" x1="0" y1="0" x2="1" y2="1"><stop offset="0" stop-color="#f5e9dd"/><stop offset="0.55" stop-color="#e6d2c0"/><stop offset="1" stop-color="#7fa8bf"/></linearGradient>
      <linearGradient id="tone-ribbon" x1="0" y1="0" x2="1" y2="1"><stop offset="0" stop-color="#b52a30"/><stop offset="0.5" stop-color="#dfc7c0"/><stop offset="1" stop-color="#f4efe8"/></linearGradient>
      <linearGradient id="tone-kiss" x1="0" y1="0" x2="1" y2="1"><stop offset="0" stop-color="#e3e3e0"/><stop offset="0.5" stop-color="#716862"/><stop offset="1" stop-color="#d8d4cf"/></linearGradient>
      <linearGradient id="tone-lane" x1="0" y1="0" x2="1" y2="1"><stop offset="0" stop-color="#2c4426"/><stop offset="0.5" stop-color="#6e7a64"/><stop offset="1" stop-color="#8f8c88"/></linearGradient>
      <linearGradient id="tone-car" x1="0" y1="0" x2="1" y2="1"><stop offset="0" stop-color="#f3f2ef"/><stop offset="0.55" stop-color="#d9d6d2"/><stop offset="1" stop-color="#5a4547"/></linearGradient>
      <linearGradient id="tone-album" x1="0" y1="0" x2="1" y2="1"><stop offset="0" stop-color="#cfcfcf"/><stop offset="0.55" stop-color="#f2f0ee"/><stop offset="1" stop-color="#2e2e2e"/></linearGradient>
    </defs>
    <polygon role="img" aria-label="Wedding rings on a warm background" fill="url(#tone-gold)" points="432,255 509,332 432,409 355,332"/>
    <polygon role="img" aria-label="Bride and groom by the sea" fill="url(#tone-sky)" points="600,255 677,332 600,409 523,332"/>
    <polygon role="img" aria-label="Bouquet of cream roses" fill="url(#tone-rose)" points="767,255 844,332 767,409 690,332"/>
    <polygon role="img" aria-label="Couple walking in a garden" fill="url(#tone-forest)" points="516,339 593,416 516,493 439,416"/>
    <polygon role="img" aria-label="Wedding gazebo by the water" fill="url(#tone-gazebo)" points="683,339 760,416 683,493 606,416"/>
    <polygon role="img" aria-label="Red ribbon on a ring cushion" fill="url(#tone-ribbon)" points="432,422 509,499 432,576 355,499"/>
    <polygon role="img" aria-label="Couple embracing" fill="url(#tone-kiss)" points="600,422 677,499 600,576 523,499"/>
    <polygon role="img" aria-label="Vintage van on a tree-lined lane" fill="url(#tone-lane)" points="767,422 844,499 767,576 690,499"/>
    <polygon role="img" aria-label="White wedding car with just married plate" fill="url(#tone-car)" points="516,506 593,583 516,660 439,583"/>
    <polygon role="img" aria-label="Printed wedding photo album" fill="url(#tone-album)" points="683,506 760,583 683,660 606,583"/>
  </svg>

  <p class="story-line">I can help you build your own story.</p>

  <a class="contact-button" href="#">
    <svg width="14" height="10" viewBox="0 0 14 10" aria-hidden="true">
      <rect x="0.5" y="0.5" width="13" height="9" fill="none" stroke="#2b2b2b"/>
      <polyline points="0.5,0.5 7,6 13.5,0.5" fill="none" stroke="#2b2b2b"/>
    </svg>
    Contact me!
  </a>

  <p class="copyright">© 2020 by Bram Kellet.</p>

  <nav class="social-links">
    <a href="#"><span class="social-dot"></span>Friendly</a>
    <a href="#"><span class="social-dot"></span>Chirp</a>
    <a href="#"><span class="social-dot"></span>Snapgram</a>
  </nav>
</body>
</html>
```